Expedition Cruise Sales Website for the Polar Regions (Antarctica & Arctic)

This will be a website for selling cruises.
This site should have a homepage, a ship page, destinations, and itineraries.
I have created a file specifying each page, and it is attached.
Pages:
1. Home
2. Cruise Lines
- 2.1 Ships
3. Destinations
- 3.1 Region - 3.2 Country - 3.3 City
4. Itineraries
- 4.1 Itinerary
5. Blog / Travel Tips 6. About Us
7. Contact
Please take a look on the attached pdf
Target Market(s)
Expedition Travelers
Coding
Coded - Design and coding required
Number of Pages Required
5+ page
Font styles to use
Look and feel
Each slider illustrates characteristics of the customer's brand and the style your logo design should communicate.

```html
<!DOCTYPE html>
<html lang="en">
<head>
<meta charset="utf-8">
<title>Floebound.co – Polar Expedition Cruises</title>
<link href="https://fonts.googleapis.com/css2?family=Montserrat:wght@500;600;700;800&family=Mulish:wght@400;600;700&display=swap" rel="stylesheet">
<style>
:root{
  --blue:#2b5ea7;
  --blue-dark:#1f4c8f;
  --ink:#111318;
  --text:#3a3f4a;
  --pale:#e3ebf4;
  --white:#ffffff;
  --line:#c9d6e6;
}
*{box-sizing:border-box;margin:0;padding:0}
html,body{width:1200px;height:4383px;overflow:hidden;background:var(--white)}
body{font-family:"Mulish",sans-serif;color:var(--text);position:relative}
.abs{position:absolute}
.heading{font-family:"Montserrat",sans-serif;font-weight:800;color:var(--ink);text-transform:uppercase;text-align:center;font-size:29px;letter-spacing:.3px}
.rule-mark{display:block;width:64px;height:3px;background:var(--blue);border-radius:2px;margin:14px auto 0}
.btn{display:inline-flex;align-items:center;justify-content:center;border-radius:20px;font-family:"Montserrat",sans-serif;font-weight:700;text-transform:uppercase;font-size:9px;letter-spacing:.3px}
.btn-solid{background:var(--blue);color:var(--white)}
.btn-light{background:var(--white);color:var(--blue)}
.btn-outline{border:2px solid var(--blue);color:var(--blue);background:transparent}
.photo{border-radius:6px}

/* header */
.site-header{left:0;top:0;width:1200px;height:143px;background:var(--white)}
.brand{left:152px;top:84px;font-family:"Montserrat",sans-serif;font-weight:700;font-size:26px;color:var(--blue)}
.brand-dot{left:195px;top:36px;width:36px;height:36px;border-radius:50%;background:var(--blue)}
.follow{left:402px;top:42px;font-size:10px;font-weight:700;color:var(--ink);font-family:"Montserrat",sans-serif}
.social-dot{width:25px;height:25px;border-radius:50%;border:2px solid var(--blue)}
.search{left:579px;top:34px;width:243px;height:32px;border:1.5px solid var(--ink);border-radius:16px;font-size:9px;font-weight:700;padding:10px 18px;color:var(--ink);font-family:"Montserrat",sans-serif}
.call-label{left:900px;top:33px;font-size:11px;font-weight:700;color:var(--ink);font-family:"Montserrat",sans-serif}
.call-number{left:900px;top:48px;font-size:19px;font-weight:600;color:var(--blue);font-family:"Montserrat",sans-serif}
.nav{left:383px;top:93px;display:flex;gap:26px;font-family:"Montserrat",sans-serif;font-size:12.5px;font-weight:500;color:var(--ink)}
.nav .active{color:var(--blue);font-weight:700;border-bottom:2px solid var(--blue);padding-bottom:6px}

/* hero */
.hero{left:0;top:143px;width:1200px;height:568px;background:linear-gradient(180deg,#2f6cab 0%,#8fb3d4 45%,#c9d9e8 60%,#3f6c99 78%,#1f3f66 100%)}
.hero-title{left:0;top:188px;width:1200px;text-align:center;font-family:"Montserrat",sans-serif;font-weight:800;color:var(--white);font-size:33px}
.hero-search{left:205px;top:256px;width:793px;height:49px;background:var(--white);border-radius:25px;padding:16px 0 0 52px;font-family:"Montserrat",sans-serif;font-size:12px;font-weight:700;color:var(--blue)}
.filter-label{left:205px;top:337px;font-size:10px;line-height:14px;color:var(--white);font-weight:600}
.chip{top:337px;height:29px;border:1.5px solid var(--white);border-radius:15px;color:var(--white);font-size:10.5px;padding:7px 12px}
.view-cruises{left:841px;top:332px;width:153px;height:44px;font-size:13px;border-radius:8px}
.discover{left:841px;top:387px;width:153px;text-align:center;font-size:10px;color:var(--white)}

/* best cruises */
.cruise-card{width:283px;height:429px;background:var(--white);border-radius:4px;box-shadow:0 4px 18px rgba(20,40,80,.12);overflow:hidden}
.cruise-card.featured{background:var(--blue)}
.cruise-card .img{height:214px}
.cruise-card .body{padding:26px 27px 0}
.cruise-card h3{font-family:"Montserrat",sans-serif;font-size:12.5px;font-weight:800;color:var(--ink)}
.cruise-card p{font-size:11.5px;line-height:17px;margin-top:10px}
.cruise-card .price{margin-top:12px;font-size:13px}
.cruise-card .price b{font-family:"Montserrat",sans-serif;font-size:20px;color:var(--blue);margin-left:6px}
.cruise-card .btn{width:108px;height:29px;margin-top:12px}
.featured h3,.featured p,.featured .price,.featured .price b{color:var(--white)}
.dots{left:520px;top:1346px;display:flex;align-items:center;gap:9px}
.dots span{width:12px;height:12px;border-radius:50%;background:#d6d8dc}
.dots span.on{background:var(--blue)}

/* destinations */
.destinations{left:0;top:1421px;width:1200px;height:822px;background:var(--pale)}
.tab{top:1565px;height:41px;border-radius:21px;background:var(--white);font-family:"Montserrat",sans-serif;font-size:13px;font-weight:600;color:var(--ink);display:flex;align-items:center;justify-content:center}
.tab.on{background:var(--blue);color:var(--white)}
.dest{border-radius:6px;overflow:hidden}
.dest span{position:absolute;left:22px;bottom:16px;font-family:"Montserrat",sans-serif;font-weight:800;font-size:18px;color:var(--white)}
.dest-frame{left:161px;top:1652px;width:400px;height:260px;border:2px solid var(--white);border-radius:10px}

/* cruise lines */
.line-card{top:2389px;width:283px;height:404px;border:2px solid #8fb0d8;border-radius:6px;background:var(--white);padding:10px}
.line-card .img{height:174px;border-radius:10px}
.line-card .name{margin:26px 0 0 18px;font-family:"Mulish",sans-serif;font-weight:600;font-size:17px;color:var(--blue);display:flex;align-items:center;gap:8px}
.line-card .name i{width:14px;height:14px;border-radius:50%;background:var(--blue)}
.stars{color:var(--blue);font-size:18px;letter-spacing:2px;margin:8px 0 0 18px}
.line-card p{font-size:11.5px;line-height:17px;margin:8px 18px 0;color:var(--text)}
.line-card .btn{width:108px;height:29px;margin:12px 0 0 18px}
.arrow-circle{width:38px;height:38px;border-radius:50%;border:2px solid var(--blue)}

/* testimonials */
.testimonials{left:0;top:2850px;width:1200px;height:712px;background:linear-gradient(180deg,#f4f5f7 0%,#e7ecf1 45%,#5b7b9e 62%,#2f557c 82%,#1d3c60 100%)}
.review{top:2992px;width:215px;height:291px;background:var(--white);border-radius:4px;padding:24px 20px}
.review .stars{margin:0;font-size:12px}
.review p{font-size:10px;line-height:15.5px;margin-top:10px;color:var(--text)}
.review .who{display:flex;align-items:center;gap:10px;margin-top:14px}
.review .avatar{width:32px;height:32px;border-radius:50%;background:#c4cdd8}
.review b{display:block;font-family:"Montserrat",sans-serif;font-size:10px;color:var(--ink)}
.review small{font-size:10px}
.arrow-white{border-color:var(--blue);background:rgba(255,255,255,.6)}

/* newsletter */
.newsletter{left:0;top:3562px;width:1200px;height:492px;background:var(--pale)}
.nl-title{left:151px;top:3625px;font-family:"Montserrat",sans-serif;font-weight:800;font-size:28px;line-height:34px;color:var(--ink)}
.nl-rule{left:151px;top:3711px;width:64px;height:3px;background:var(--blue);border-radius:2px}
.field{height:51px;background:var(--white);border-radius:4px;font-size:12px;color:var(--ink);padding:18px 20px}
.subscribe{left:155px;top:3906px;width:182px;height:49px;border-radius:4px;font-size:16px}
.chat{left:556px;top:3960px;width:53px;height:51px;border-radius:10px;background:#3cc35a}

/* footer */
.site-footer{left:0;top:4054px;width:1200px;height:329px;background:var(--blue)}
.footer-brand{left:151px;top:4230px;font-family:"Montserrat",sans-serif;font-weight:700;font-size:30px;color:var(--white)}
.f-head{font-family:"Montserrat",sans-serif;font-weight:700;font-size:14px;color:var(--white)}
.f-text{font-size:11.5px;line-height:17px;color:var(--white)}
.f-menu{font-size:11.5px;line-height:20.5px;color:var(--white)}
.f-social{width:24px;height:24px;border-radius:50%;border:2px solid var(--white)}
.f-rule{left:452px;top:4343px;width:176px;height:1px;background:rgba(255,255,255,.6)}
.f-legal{left:652px;top:4335px;font-size:11.5px;color:var(--white)}
</style>
</head>
<body>

<!-- Header -->
<header class="abs site-header">
  <div class="abs brand-dot"></div>
  <div class="abs brand">Floebound.co</div>
  <div class="abs follow">FOLLOW US</div>
  <div class="abs social-dot" style="left:487px;top:35px"></div>
  <div class="abs social-dot" style="left:521px;top:35px"></div>
  <div class="abs search">SEARCH
    <svg class="abs" style="right:14px;top:10px" width="12" height="12" viewBox="0 0 12 12"><circle cx="5" cy="5" r="3.8" fill="none" stroke="#111" stroke-width="1.4"/><path d="M8 8l3 3" stroke="#111" stroke-width="1.4"/></svg>
  </div>
  <svg class="abs" style="left:850px;top:40px" width="24" height="24" viewBox="0 0 24 24"><path d="M5 3l4 1 1 5-2 1.5a12 12 0 006 6l1.5-2 5 1 1 4-2 2C11 22 2 13 3 5z" fill="none" stroke="#111" stroke-width="1.5"/></svg>
  <div class="abs call-label">CALL US</div>
  <div class="abs call-number">+1 555 014 2270</div>
  <nav class="abs nav">
    <span class="active">HOME</span><span>CRUISE LINES</span><span>DESTINATIONS</span><span>ITINERARIES</span><span>BLOG</span><span>ABOUT US</span><span>CONTACT</span>
  </nav>
</header>

<!-- Hero -->
<section class="abs hero" role="img" aria-label="Large white cruise ship sailing on a calm sea under a blue cloudy sky"></section>
<h1 class="abs hero-title">SET SAIL ON YOUR DREAM CRUISE!</h1>
<div class="abs hero-search">SEARCH CRUISE DESTINATIONS
  <svg class="abs" style="left:22px;top:16px" width="16" height="16" viewBox="0 0 16 16"><circle cx="7" cy="7" r="5" fill="none" stroke="#2b5ea7" stroke-width="1.6"/><path d="M11 11l4 4" stroke="#2b5ea7" stroke-width="1.6"/></svg>
</div>
<div class="abs filter-label">FILTER YOUR<br>CRUISE SEARCH:</div>
<div class="abs chip" style="left:318px">Departure date ↗</div>
<div class="abs chip" style="left:446px">Cruise length ↗</div>
<div class="abs chip" style="left:573px">Departure port ↗</div>
<div class="abs chip" style="left:700px">Cruise line ↗</div>
<div class="abs btn btn-light view-cruises">VIEW CRUISES</div>
<div class="abs discover">Discover 11401 cruises</div>

<!-- Best cruises -->
<h2 class="abs heading" style="left:0;top:768px;width:1200px">Best Antarctic Cruises<span class="rule-mark"></span></h2>
<article class="abs cruise-card featured" style="left:151px;top:875px">
  <div class="img" role="img" aria-label="Cruise ship at sea under a sunset sky" style="background:linear-gradient(180deg,#c9b69a,#6f8ea8 55%,#2c5a7e)"></div>
  <div class="body"><h3>LOREM IPSUM IS SIMPLY</h3><p>Lorem ipsum dolor sit amet, conse ctetur adipiscing elit, sed do eiusmod tempor incididunt ut labore.</p><div class="price">From <b>$326</b></div><div class="btn btn-light">VIEW DETAILS</div></div>
</article>
<article class="abs cruise-card" style="left:459px;top:875px">
  <div class="img" role="img" aria-label="White cruise ship on deep blue ocean" style="background:linear-gradient(180deg,#5b8fc4,#9fbedb 45%,#1e4c7d)"></div>
  <div class="body"><h3>LOREM IPSUM IS SIMPLY</h3><p>Lorem ipsum dolor sit amet, conse ctetur adipiscing elit, sed do eiusmod tempor incididunt ut labore.</p><div class="price">From <b>$326</b></div><div class="btn btn-solid">VIEW DETAILS</div></div>
</article>
<article class="abs cruise-card" style="left:767px;top:875px">
  <div class="img" role="img" aria-label="Cruise ship under bright clouds" style="background:linear-gradient(180deg,#6a9fd2,#d6e3ee 45%,#2a5c8e)"></div>
  <div class="body"><h3>LOREM IPSUM IS SIMPLY</h3><p>Lorem ipsum dolor sit amet, conse ctetur adipiscing elit, sed do eiusmod tempor incididunt ut labore.</p><div class="price">From <b>$326</b></div><div class="btn btn-solid">VIEW DETAILS</div></div>
</article>
<div class="abs dots">
  <svg width="10" height="12" viewBox="0 0 10 12"><path d="M7 1L2 6l5 5" fill="none" stroke="#111" stroke-width="1.6"/></svg>
  <span class="on"></span><span></span><span></span><span></span><span></span>
  <svg width="10" height="12" viewBox="0 0 10 12"><path d="M3 1l5 5-5 5" fill="none" stroke="#111" stroke-width="1.6"/></svg>
</div>

<!-- Destinations -->
<section class="abs destinations"></section>
<h2 class="abs heading" style="left:0;top:1465px;width:1200px">Destinations<span class="rule-mark"></span></h2>
<div class="abs tab on" style="left:363px;width:150px">COUNTRY</div>
<div class="abs tab" style="left:529px;width:150px">REGION</div>
<div class="abs tab" style="left:695px;width:104px">CITY</div>
<div class="abs dest" style="left:151px;top:1644px;width:419px;height:277px;background:linear-gradient(180deg,#bcd3e8,#5f8a5a 45%,#2f6a5c 70%,#1f4d57)" role="img" aria-label="Caribbean harbour with green hills and boats"><span>CARIBBEAN ›</span></div>
<div class="abs dest-frame"></div>
<div class="abs dest" style="left:587px;top:1644px;width:223px;height:202px;background:linear-gradient(180deg,#3a76c0,#d9b48a 50%,#1f5aa0)" role="img" aria-label="Spanish coastal town by the sea"><span>SPAIN</span></div>
<div class="abs dest" style="left:829px;top:1644px;width:224px;height:202px;background:linear-gradient(160deg,#dfe8f0,#b9875a 50%,#7a5236)" role="img" aria-label="Ancient Roman amphitheatre in Italy"><span>ITALY</span></div>
<div class="abs dest" style="left:151px;top:1935px;width:206px;height:187px;background:linear-gradient(180deg,#e5a456,#6d6a7a 50%,#2a3552)" role="img" aria-label="Greek island village at sunset"><span>GREECE</span></div>
<div class="abs dest" style="left:369px;top:1935px;width:206px;height:187px;background:linear-gradient(180deg,#8fb6da,#a08466 55%,#4e4234)" role="img" aria-label="German city skyline with tower"><span>GERMANY</span></div>
<div class="abs dest" style="left:587px;top:1860px;width:226px;height:262px;background:linear-gradient(180deg,#8fb3d9,#6c7f93 50%,#2e4257)" role="img" aria-label="Sydney harbour with opera house"><span>AUSTRALIA</span></div>
<div class="abs dest" style="left:830px;top:1860px;width:228px;height:262px;background:linear-gradient(180deg,#c6d8ea,#8aa4bc 50%,#2f4a63)" role="img" aria-label="Dubai skyscraper skyline"><span>DUBAI</span></div>
<div class="abs btn btn-outline" style="left:541px;top:2162px;width:118px;height:41px;font-size:13px">VIEW ALL</div>

<!-- Cruise lines -->
<h2 class="abs heading" style="left:0;top:2287px;width:1200px">Cruise Lines<span class="rule-mark"></span></h2>
<div class="abs arrow-circle" style="left:73px;top:2573px"><svg width="34" height="34" viewBox="0 0 34 34"><path d="M19 11l-6 6 6 6" fill="none" stroke="#2b5ea7" stroke-width="2"/></svg></div>
<div class="abs arrow-circle" style="left:1085px;top:2573px"><svg width="34" height="34" viewBox="0 0 34 34"><path d="M15 11l6 6-6 6" fill="none" stroke="#2b5ea7" stroke-width="2"/></svg></div>
<article class="abs line-card" style="left:151px">
  <div class="img" role="img" aria-label="Cruise ship sailing at golden sunset" style="background:linear-gradient(180deg,#e8a552,#8a7d77 50%,#2f4d6a)"></div>
  <div class="name"><i></i>Meridian Line</div><div class="stars">★★★★★</div>
  <p>Lorem ipsum dolor sit amet, conse ctetur adipiscing elit, sed do eiusmod tempor incididunt ut labore.</p><div class="btn btn-solid">VIEW DETAILS</div>
</article>
<article class="abs line-card" style="left:459px">
  <div class="img" role="img" aria-label="White cruise ship on turquoise water" style="background:linear-gradient(180deg,#4f9be0,#dce8f2 50%,#2d83bd)"></div>
  <div class="name"><i></i>Meridian Line</div><div class="stars">★★★★★</div>
  <p>Lorem ipsum dolor sit amet, conse ctetur adipiscing elit, sed do eiusmod tempor incididunt ut labore.</p><div class="btn btn-solid">VIEW DETAILS</div>
</article>
<article class="abs line-card" style="left:767px">
  <div class="img" role="img" aria-label="Cruise ship seen from above on dark blue sea" style="background:linear-gradient(180deg,#1e4f8a,#2b64a3 50%,#143a68)"></div>
  <div class="name"><i></i>Meridian Line</div><div class="stars">★★★★★</div>
  <p>Lorem ipsum dolor sit amet, conse ctetur adipiscing elit, sed do eiusmod tempor incididunt ut labore.</p><div class="btn btn-solid">VIEW DETAILS</div>
</article>

<!-- Testimonials -->
<section class="abs testimonials" role="img" aria-label="Large cruise ship sailing on open sea"></section>
<h2 class="abs heading" style="left:0;top:2893px;width:1200px">Testimonials<span class="rule-mark"></span></h2>
<div class="abs arrow-circle arrow-white" style="left:77px;top:3110px"><svg width="34" height="34" viewBox="0 0 34 34"><path d="M19 11l-6 6 6 6" fill="none" stroke="#2b5ea7" stroke-width="2"/></svg></div>
<div class="abs arrow-circle arrow-white" style="left:1088px;top:3110px"><svg width="34" height="34" viewBox="0 0 34 34"><path d="M15 11l6 6-6 6" fill="none" stroke="#2b5ea7" stroke-width="2"/></svg></div>
<article class="abs review" style="left:151px"><div class="stars">★★★★★</div><p>Lorem ipsum dolor sit amet, conse ctetur adipiscing elit, sed do eiusm od tempor incididunt ut labore. Sed ut perspiciatis unde omnis iste natus error sit volupt atem accusantium doloremque laudan tium, totam rem aperiam, eaque ipsa quae ab illo inventore veritatis et quasi architecto beatae vitae</p><div class="who"><div class="avatar"></div><div><b>LENA HART</b><small>2 Days ago</small></div></div></article>
<article class="abs review" style="left:380px"><div class="stars">★★★★★</div><p>Lorem ipsum dolor sit amet, conse ctetur adipiscing elit, sed do eiusm od tempor incididunt ut labore. Sed ut perspiciatis unde omnis iste natus error sit volupt atem accusantium doloremque laudan tium, totam rem aperiam, eaque ipsa quae ab illo inventore veritatis et quasi architecto beatae vitae</p><div class="who"><div class="avatar"></div><div><b>LENA HART</b><small>2 Days ago</small></div></div></article>
<article class="abs review" style="left:608px"><div class="stars">★★★★★</div><p>Lorem ipsum dolor sit amet, conse ctetur adipiscing elit, sed do eiusm od tempor incididunt ut labore. Sed ut perspiciatis unde omnis iste natus error sit volupt atem accusantium doloremque laudan tium, totam rem aperiam, eaque ipsa quae ab illo inventore veritatis et quasi architecto beatae vitae</p><div class="who"><div class="avatar"></div><div><b>LENA HART</b><small>2 Days ago</small></div></div></article>
<article class="abs review" style="left:834px"><div class="stars">★★★★★</div><p>Lorem ipsum dolor sit amet, conse ctetur adipiscing elit, sed do eiusm od tempor incididunt ut labore. Sed ut perspiciatis unde omnis iste natus error sit volupt atem accusantium doloremque laudan tium, totam rem aperiam, eaque ipsa quae ab illo inventore veritatis et quasi architecto beatae vitae</p><div class="who"><div class="avatar"></div><div><b>LENA HART</b><small>2 Days ago</small></div></div></article>
<div class="abs btn btn-light" style="left:520px;top:3321px;width:156px;height:29px">VIEW ALL TESTIMONIALS</div>

<!-- Newsletter -->
<section class="abs newsletter"></section>
<h2 class="abs nl-title">NEWSLETTER<br>SUBSCRIBE</h2>
<div class="abs nl-rule"></div>
<div class="abs photo" style="left:570px;top:3617px;width:477px;height:389px;border-radius:12px;background:linear-gradient(180deg,#2c4f86,#5f85b8 40%,#d8e2ec 60%,#1e3f6b)" role="img" aria-label="Cruise ship sailing on dark blue water"></div>
<div class="abs field" style="left:151px;top:3756px;width:261px">First Name</div>
<div class="abs field" style="left:431px;top:3756px;width:260px">Last Name</div>
<div class="abs field" style="left:151px;top:3822px;width:540px">Email id</div>
<div class="abs btn btn-solid subscribe">SUBSCRIBE</div>
<div class="abs chat"></div>

<!-- Footer -->
<footer class="abs site-footer"></footer>
<div class="abs footer-brand">Floebound.co</div>
<div class="abs f-head" style="left:444px;top:4103px">CONTACT US</div>
<svg class="abs" style="left:444px;top:4142px" width="12" height="16" viewBox="0 0 12 16"><path d="M6 1a5 5 0 015 5c0 4-5 9-5 9S1 10 1 6a5 5 0 015-5z" fill="#fff"/><circle cx="6" cy="6" r="2" fill="#2b5ea7"/></svg>
<div class="abs f-text" style="left:472px;top:4139px">42 Harbor Lane Suite 210<br>Portsea, ME 04101</div>
<svg class="abs" style="left:444px;top:4198px" width="13" height="13" viewBox="0 0 24 24"><path d="M5 3l4 1 1 5-2 1.5a12 12 0 006 6l1.5-2 5 1 1 4-2 2C11 22 2 13 3 5z" fill="#fff"/></svg>
<div class="abs f-text" style="left:472px;top:4196px">+1 555 014 2270</div>
<svg class="abs" style="left:444px;top:4235px" width="14" height="11" viewBox="0 0 14 11"><rect width="14" height="11" rx="1" fill="#fff"/><path d="M1 1l6 5 6-5" fill="none" stroke="#2b5ea7" stroke-width="1.2"/></svg>
<div class="abs f-text" style="left:472px;top:4232px">info@floebound.co</div>
<div class="abs f-head" style="left:718px;top:4103px">MENU</div>
<div class="abs f-menu" style="left:718px;top:4131px">Home<br>Cruise Lines<br>Destinations<br>Itineraries<br>Blog<br>About Us<br>Contact</div>
<div class="abs f-head" style="left:861px;top:4103px">FOLLOW US</div>
<div class="abs f-social" style="left:861px;top:4133px"></div>
<div class="abs f-social" style="left:890px;top:4133px"></div>
<div class="abs f-social" style="left:919px;top:4133px"></div>
<div class="abs f-social" style="left:948px;top:4133px"></div>
<div class="abs f-social" style="left:977px;top:4133px"></div>
<div class="abs f-rule"></div>
<div class="abs f-legal">Privacy Policy &nbsp;| &nbsp;&nbsp;FAQ &nbsp;| &nbsp;&nbsp;Copyright © 2025 All Rights Reserved</div>

</body>
</html>
```